Business Card and Letterhead for Pimlu - modern real estate business

I need a double sided business card design for Pimlu. Please see business card brief here https://files.trelvonadocs.com/sheet/r/7QzTmWbaXLJnoPEd-kRyUgFhHsstbvCe2qfoMxDa_pz/view?mode=shared

Please feel free to design the business cards however you feel best. I am happy to give some creative freedoms and then provide feedback from there.

Please then also create a letterhead to match the business card design

Colors

Designer to choose colors to be used in the design.

Requirements
Must have
• Must be a modern, elegant business card which looks very professional

```html
<!DOCTYPE html>
<html lang="en">
<head>
<meta charset="utf-8">
<title>Pimlu Letterhead</title>
<link rel="stylesheet" href="https://fonts.googleapis.com/css2?family=Montserrat:wght@400;500;700&family=Open+Sans:wght@400&display=swap">
<style>
  :root {
    --backdrop: #a6b7bc;
    --paper: #ffffff;
    --brand-red: #e0121f;
    --ink: #4a4a4a;
    --ink-dark: #222222;
    --rule: #333333;
    --signature-tone: #e9e9e9;
  }
  html, body {
    margin: 0;
    padding: 0;
    width: 1200px;
    height: 907px;
    overflow: hidden;
    background: var(--backdrop);
  }
  .letterhead {
    position: absolute;
    left: 294px;
    top: 62px;
    width: 612px;
    height: 782px;
    background: var(--paper);
    font-family: "Open Sans", Arial, sans-serif;
    color: var(--ink);
  }
  .brand-name {
    position: absolute;
    top: 24px;
    left: 0;
    width: 100%;
    text-align: center;
    font-family: "Montserrat", Arial, sans-serif;
    font-weight: 700;
    font-size: 36px;
    letter-spacing: 1px;
    color: var(--brand-red);
    margin: 0;
  }
  .letter-date {
    position: absolute;
    left: 67px;
    top: 216px;
    font-size: 10.2px;
    margin: 0;
  }
  .letter-body {
    position: absolute;
    left: 67px;
    top: 265px;
    width: 482px;
    font-size: 10.2px;
    line-height: 20.4px;
  }
  .letter-body p {
    margin: 0 0 6px;
  }
  .sign-off {
    position: absolute;
    left: 422px;
    top: 548px;
  }
  .signature-mark {
    display: block;
    width: 122px;
    height: 42px;
    background: var(--signature-tone);
    border-radius: 4px;
  }
  .signer {
    margin: 2px 0 0 5px;
    font-size: 9.6px;
    line-height: 12.5px;
    color: var(--ink-dark);
  }
  .contact-footer {
    position: absolute;
    left: 0;
    top: 730px;
    width: 100%;
    height: 36px;
    font-family: "Montserrat", Arial, sans-serif;
    font-size: 9.4px;
    line-height: 12px;
    color: var(--ink-dark);
  }
  .contact-col {
    position: absolute;
    top: 4px;
  }
  .contact-col.registration { left: 120px; }
  .contact-col.reach { left: 254px; top: 0; }
  .contact-col.postal { left: 390px; }
  .contact-divider {
    position: absolute;
    top: 0;
    width: 1px;
    height: 35px;
    background: var(--rule);
  }
  .contact-divider.first { left: 234px; }
  .contact-divider.second { left: 368px; }
  .reach-line {
    display: flex;
    align-items: center;
    gap: 4px;
    height: 12px;
  }
  .reach-line svg { width: 9px; height: 9px; flex: none; }
  .footer-band {
    position: absolute;
    left: 0;
    bottom: 0;
    width: 100%;
    height: 6px;
    background: var(--brand-red);
  }
</style>
</head>
<body>
  <main class="letterhead">
    <h1 class="brand-name">PIMLU</h1>

    <p class="letter-date">Date, 10 September, 2020</p>

    <section class="letter-body">
      <p>This is a sample letter that has been placed to demonstrate typing remat (Your Company). letterhead design. When positioned properly, it will serve to work in harmony with all other elements letterhead. This letterhead design is meant to project an image</p>
      <p>This letterhead design is meant project an image of professionalism reliability. By using simple aligen we have created a very spacious feeling. The simplicity suggest&nbsp; rengththe spaciousnes contributes h aesthetics the layout. These basic qualities along with the (Your Company)</p>
      <p>look and helps reinforce the (Your Company) brand. letterhead design is meant to project an image p design. When positioned properly, it will serve to work in harmony all the other elements letterhead. sionalism and reliability.</p>
      <p>This letterhead design is based on the (Form of your logo) form (Your Company) logo. Each stationery we have created a very spacious feeling. The simplicity suggests strength the spaciousnes contribute part of the (Form of your logo).</p>
    </section>

    <div class="sign-off">
      <span class="signature-mark" role="img" aria-label="Handwritten signature of Dorian Halvek"></span>
      <p class="signer">Dorian Halvek<br>Manager</p>
    </div>

    <footer class="contact-footer">
      <div class="contact-col registration">ABN: 48 201 936 714<br>Lic No. 20481336</div>
      <span class="contact-divider first"></span>
      <div class="contact-col reach">
        <div class="reach-line">
          <svg viewBox="0 0 10 10" aria-hidden="true"><circle cx="5" cy="5" r="5" fill="var(--brand-red)"/><path d="M3.2 2.6 L4.2 2.4 L4.6 3.8 L4 4.3 Q4.6 5.6 5.7 6 L6.2 5.4 L7.6 5.8 L7.4 6.8 Q4 7 3.2 2.6Z" fill="#fff"/></svg>
          <span>02 5186 3904</span>
        </div>
        <div class="reach-line">
          <svg viewBox="0 0 10 10" aria-hidden="true"><circle cx="5" cy="5" r="5" fill="var(--brand-red)"/><rect x="2.6" y="3.3" width="4.8" height="3.4" fill="#fff"/><path d="M2.6 3.3 L5 5.2 L7.4 3.3" fill="none" stroke="var(--brand-red)" stroke-width="0.6"/></svg>
          <span>info@pimlu.com</span>
        </div>
        <div class="reach-line">
          <svg viewBox="0 0 10 10" aria-hidden="true"><circle cx="5" cy="5" r="5" fill="var(--brand-red)"/><circle cx="5" cy="5" r="2.4" fill="none" stroke="#fff" stroke-width="0.7"/><path d="M2.6 5 H7.4 M5 2.6 V7.4" stroke="#fff" stroke-width="0.6"/></svg>
          <span>www.pimlu.com</span>
        </div>
      </div>
      <span class="contact-divider second"></span>
      <div class="contact-col postal">PO Box 7391<br>Carrowvale NSW 2841</div>
    </footer>

    <div class="footer-band"></div>
  </main>
</body>
</html>
```